Media Services Start-up -- Corporate Website and Logo Design. Inspiration required!

We need a logo design and corporate website design, including coding, for our start-up business.
Vennatra’s value proposition is based on bringing together media content from a vast number of geographies globally, adding human and AI curation, translation and editing, and delivering the content using tailored customer interfaces. On the one hand, the business brings together media coverage from all over the world, and on the other it brings together content, human skills and technology to deliver a supreme customer experience.
Vennatra is a B2B media monitoring and analytics business with emphasis on global customers. Vennatra's service offering is centred around sourcing media content from different markets, processing, storing and delivering the content and insights derived from it using an online platform / mobile app.
The messaging we want to create through the logo is:
- Global scope
- Speed of delivery
- Cost-efficiency
- Multi-lingual
- Tailor-made
- Trustworthy
Target Market(s)
Business to business, PR / Communications, Media, Marketing
Logo Text
Vennatra
Coding
Coded - Design and coding required
Number of Pages Required
5+ page
Font styles to use
Other font styles liked:
- See Design Brief for details
Colors
Designer to choose colors to be used in the design.

```html
<!DOCTYPE html>
<html lang="en">
<head>
<meta charset="utf-8">
<title>Vennatra — Global Media Intelligence</title>
<link href="https://fonts.googleapis.com/css2?family=Roboto:wght@500;700;900&family=Open+Sans:wght@400;600&display=swap" rel="stylesheet">
<style>
:root{
  --page:#ebebeb;
  --white:#ffffff;
  --blue:#0088cc;
  --blue-deep:#0068a8;
  --blue-dark:#025e99;
  --blue-pale:#e2eff8;
  --orange:#ff8c00;
  --ink:#2b2b2b;
  --text:#5a5a5a;
  --footer:#262626;
}
*{box-sizing:border-box;margin:0;padding:0}
html,body{width:1200px;height:4501px;overflow:hidden;background:var(--page)}
body{position:relative;font-family:"Open Sans",Arial,sans-serif;color:var(--text)}
.board{position:absolute;left:75px;width:1050px;background:var(--white);overflow:hidden}
.board-home{top:66px;height:792px}
.board-solution{top:983px;height:3415px}
.logo{position:absolute;font-family:"Roboto",Arial,sans-serif;font-weight:700;font-size:23px;color:var(--white);letter-spacing:.3px}
.nav{position:absolute;display:flex;gap:19px;font-family:"Roboto",Arial,sans-serif;font-weight:700;font-size:12.5px;color:var(--white);list-style:none}
.nav .active{color:var(--orange)}
.hero-bg{position:absolute;left:0;top:0}
.art{position:absolute;border-radius:6px}
.hero-title{position:absolute;left:523px;top:108px;font-family:"Roboto",Arial,sans-serif;font-weight:700;font-size:38px;line-height:44px;color:var(--white)}
.hero-text{position:absolute;left:523px;top:200px;width:430px;font-size:14.5px;line-height:24.5px;color:var(--white);text-align:justify}
.lead-form{position:absolute;left:526px;top:342px;width:427px;height:418px;background:var(--blue-deep)}
.lead-form h2{position:absolute;top:38px;width:100%;text-align:center;font-family:"Roboto",Arial,sans-serif;font-size:16px;font-weight:700;color:var(--white)}
.field{position:absolute;left:40px;width:346px;height:49px;background:var(--white);font-size:12.5px;color:#666;padding:16px 10px}
.btn{position:absolute;left:40px;top:315px;width:346px;height:49px;background:var(--orange);color:var(--white);font-family:"Roboto",Arial,sans-serif;font-weight:700;font-size:14px;text-align:center;line-height:49px}
.legal{position:absolute;left:94px;top:744px;font-size:13px;color:#444}
.top-band{position:absolute;left:0;top:0;width:1050px;height:59px;background:var(--blue-dark)}
.banner{position:absolute;left:0;top:59px;width:1050px;height:241px;background:linear-gradient(90deg,#0a6fae,#066aa6 60%,#0a5f95)}
.banner-title{position:absolute;left:433px;top:148px;font-family:"Roboto",Arial,sans-serif;font-weight:700;font-size:38px;color:var(--white)}
.section-title{position:absolute;font-family:"Roboto",Arial,sans-serif;font-weight:700;font-size:26px;color:var(--ink);letter-spacing:.2px}
.intro{position:absolute;font-size:13.5px;line-height:24.5px;text-align:justify}
.points{position:absolute;list-style:none;font-size:13.5px;line-height:24.5px}
.points li{position:relative;padding-left:36px;margin-bottom:25px}
.points li svg{position:absolute;left:0;top:6px}
.slab{position:absolute}
.footer{position:absolute;left:0;top:3127px;width:1050px;height:288px;background:var(--footer);color:var(--white);text-align:center}
.footer h3{position:absolute;top:56px;width:100%;font-family:"Roboto",Arial,sans-serif;font-weight:700;font-size:26px}
.footer p{position:absolute;top:96px;left:225px;width:600px;font-size:13.5px;line-height:24.5px}
.contacts{position:absolute;top:168px;left:0;width:100%;display:flex;justify-content:center;gap:78px;font-size:13.5px;list-style:none}
.contacts li{display:flex;align-items:center;gap:14px}
.footer .copy{position:absolute;top:236px;width:100%;font-size:13.5px}
</style>
</head>
<body>

<section class="board board-home">
  <svg class="hero-bg" width="1050" height="792" viewBox="0 0 1050 792" aria-hidden="true">
    <defs>
      <linearGradient id="heroGrad" x1="0" y1="0" x2="1" y2="1">
        <stop offset="0" stop-color="#0a7fc2"/>
        <stop offset="1" stop-color="#0068a8"/>
      </linearGradient>
    </defs>
    <polygon points="0,0 1050,0 1050,541 950,571 950,600 526,597 0,566" fill="url(#heroGrad)"/>
    <polygon points="0,536 526,570 526,597 0,566" fill="#1a8fd0"/>
  </svg>
  <div class="logo" style="left:96px;top:22px">VENNATRA</div>
  <ul class="nav" style="left:405px;top:36px">
    <li class="active">HOME</li><li>ABOUT US</li><li>SOLUTIONS</li><li>HOW WE DO IT</li><li>OUR PEOPLE</li><li>TECHNOLOGY</li>
  </ul>
  <div class="art" role="img" aria-label="Illustration of web pages on a monitor and floating screens showing family health content" style="left:0;top:108px;width:501px;height:350px;background:linear-gradient(135deg,#5fb6e6,#1688c8)"></div>
  <h1 class="hero-title">DELIVERING GLOBAL<br>MEDIA INTELLIGENCE</h1>
  <p class="hero-text">Vennatra is an international media intelligence service provider. We help communications teams build and operate truly global media monitoring and measurement programmes.</p>
  <form class="lead-form">
    <h2>LEARN MOREABOUT VENNATRA</h2>
    <div class="field" style="top:91px">Name</div>
    <div class="field" style="top:165px">Email</div>
    <div class="field" style="top:240px">Phone</div>
    <div class="btn">GET STARTED</div>
  </form>
  <p class="legal">Copyrights 2019 | Vennatra All Rights are Reserved</p>
</section>

<section class="board board-solution">
  <div class="top-band"></div>
  <div class="banner">
    <div class="art" role="img" aria-label="Isometric illustration of analytics dashboards with people" style="left:80px;top:0;width:330px;height:241px;background:linear-gradient(135deg,#4aa6dc,#0f74b4);border-radius:0"></div>
    <div class="art" role="img" aria-label="Illustration of a person walking while looking at a phone" style="left:830px;top:50px;width:120px;height:191px;background:linear-gradient(180deg,#0b5f96,#08507f);border-radius:0"></div>
    <div class="banner-title">SOLUTION</div>
  </div>
  <div class="logo" style="left:96px;top:14px">VENNATRA</div>
  <ul class="nav" style="left:405px;top:21px">
    <li class="active">HOME</li><li>ABOUT US</li><li>SOLUTIONS</li><li>HOW WE DO IT</li><li>OUR PEOPLE</li><li>TECHNOLOGY</li>
  </ul>

  <!-- Content sourcing -->
  <h2 class="section-title" style="left:96px;top:375px">CONTENT SOURCING</h2>
  <p class="intro" style="left:96px;top:421px;width:420px">We help you build a content strategy that meets your budget coverage needs across earned media - Print, Online, TV and Radio.</p>
  <ul class="points" style="left:96px;top:484px;width:440px">
    <li><svg width="13" height="13" viewBox="0 0 13 13"><circle cx="6.5" cy="6.5" r="5.5" fill="none" stroke="#0088cc" stroke-width="1.6"/><path d="M4 6.7l1.8 1.7L9 5" fill="none" stroke="#0088cc" stroke-width="1.6"/></svg>Identify geographies and markets of interest</li>
    <li><svg width="13" height="13" viewBox="0 0 13 13"><circle cx="6.5" cy="6.5" r="5.5" fill="none" stroke="#0088cc" stroke-width="1.6"/><path d="M4 6.7l1.8 1.7L9 5" fill="none" stroke="#0088cc" stroke-width="1.6"/></svg>Build target media source lists to fulfil monitoring and measurement requirements</li>
    <li><svg width="13" height="13" viewBox="0 0 13 13"><circle cx="6.5" cy="6.5" r="5.5" fill="none" stroke="#0088cc" stroke-width="1.6"/><path d="M4 6.7l1.8 1.7L9 5" fill="none" stroke="#0088cc" stroke-width="1.6"/></svg>Using our transparent cost calculator, we help you with accurate budgeting and choices to ensure you meet your strategy and objectives</li>
    <li><svg width="13" height="13" viewBox="0 0 13 13"><circle cx="6.5" cy="6.5" r="5.5" fill="none" stroke="#0088cc" stroke-width="1.6"/><path d="M4 6.7l1.8 1.7L9 5" fill="none" stroke="#0088cc" stroke-width="1.6"/></svg>Translate and localise keyword searches and editorial instructions into effecient source-/ country-/ provider-specific needs to minimise wasted content.</li>
  </ul>
  <div class="art" role="img" aria-label="Illustration of a person on a video call at a desk with a plant" style="left:554px;top:402px;width:415px;height:250px;background:var(--blue-pale);border-radius:60px 60px 20px 20px"></div>
  <svg class="slab" style="left:579px;top:645px" width="373" height="117" aria-hidden="true"><polygon points="0,0 373,38 373,117 0,79" fill="var(--blue)"/></svg>

  <!-- Content collection -->
  <div class="art" role="img" aria-label="Illustration of a woman holding thumbs up and thumbs down cards beside a blue shape" style="left:96px;top:852px;width:374px;height:270px;background:linear-gradient(135deg,#e9f3fa,#cfe4f3)"></div>
  <svg class="slab" style="left:96px;top:1127px" width="374" height="117" aria-hidden="true"><polygon points="0,38 374,0 374,79 0,117" fill="var(--blue)"/></svg>
  <h2 class="section-title" style="left:510px;top:967px">CONTENT COLLECTION</h2>
  <ul class="points" style="left:510px;top:1039px;width:445px">
    <li><svg width="13" height="13" viewBox="0 0 13 13"><circle cx="6.5" cy="6.5" r="5.5" fill="none" stroke="#0088cc" stroke-width="1.6"/><path d="M4 6.7l1.8 1.7L9 5" fill="none" stroke="#0088cc" stroke-width="1.6"/></svg>We consolidate and manage the delivery of your global media content into a Cloud-based scalable media platform, taking the headache of content management away from your teams.</li>
  </ul>

  <!-- Content augmentation -->
  <h2 class="section-title" style="left:96px;top:1350px">CONTENT AUGMENTATION</h2>
  <ul class="points" style="left:96px;top:1428px;width:440px">
    <li><svg width="13" height="13" viewBox="0 0 13 13"><circle cx="6.5" cy="6.5" r="5.5" fill="none" stroke="#0088cc" stroke-width="1.6"/><path d="M4 6.7l1.8 1.7L9 5" fill="none" stroke="#0088cc" stroke-width="1.6"/></svg>We manage and normalise all of the source-level reference: country, language, reach etc.</li>
    <li><svg width="13" height="13" viewBox="0 0 13 13"><circle cx="6.5" cy="6.5" r="5.5" fill="none" stroke="#0088cc" stroke-width="1.6"/><path d="M4 6.7l1.8 1.7L9 5" fill="none" stroke="#0088cc" stroke-width="1.6"/></svg>We add editorial validation to ensure only the content required reaches your delivery, removing inevitable noise from source providers</li>
    <li><svg width="13" height="13" viewBox="0 0 13 13"><circle cx="6.5" cy="6.5" r="5.5" fill="none" stroke="#0088cc" stroke-width="1.6"/><path d="M4 6.7l1.8 1.7L9 5" fill="none" stroke="#0088cc" stroke-width="1.6"/></svg>Tagging - AI and human based tagging to detect locations, people, topics, products, brands, services, etc.</li>
    <li><svg width="13" height="13" viewBox="0 0 13 13"><circle cx="6.5" cy="6.5" r="5.5" fill="none" stroke="#0088cc" stroke-width="1.6"/><path d="M4 6.7l1.8 1.7L9 5" fill="none" stroke="#0088cc" stroke-width="1.6"/></svg>Human and automated grouping of stories across geographies: clustering, "also-in" groupings etc.</li>
    <li><svg width="13" height="13" viewBox="0 0 13 13"><circle cx="6.5" cy="6.5" r="5.5" fill="none" stroke="#0088cc" stroke-width="1.6"/><path d="M4 6.7l1.8 1.7L9 5" fill="none" stroke="#0088cc" stroke-width="1.6"/></svg>Translation summarisation - AI Translation or human-created depending on budget, speed of delivery and need.</li>
    <li><svg width="13" height="13" viewBox="0 0 13 13"><circle cx="6.5" cy="6.5" r="5.5" fill="none" stroke="#0088cc" stroke-width="1.6"/><path d="M4 6.7l1.8 1.7L9 5" fill="none" stroke="#0088cc" stroke-width="1.6"/></svg>Digest authoring - refining the essence of today's coverage into a concise board-ready output for your organisation</li>
  </ul>
  <div class="art" role="img" aria-label="Illustration of a woman with a phone among stylised trees and social reaction icons" style="left:550px;top:1406px;width:446px;height:310px;background:linear-gradient(180deg,#eef5fb,#d5e8f5)"></div>
  <svg class="slab" style="left:578px;top:1745px" width="374" height="117" aria-hidden="true"><polygon points="0,0 374,38 374,117 0,79" fill="var(--blue)"/></svg>

  <!-- Content delivery -->
  <div class="art" role="img" aria-label="Illustration of a man running after a delivery drone in a city" style="left:79px;top:1995px;width:391px;height:290px;background:linear-gradient(180deg,#e6f1fa,#cfe3f2)"></div>
  <svg class="slab" style="left:96px;top:2277px" width="374" height="117" aria-hidden="true"><polygon points="0,38 374,0 374,79 0,117" fill="var(--blue)"/></svg>
  <h2 class="section-title" style="left:510px;top:1997px">CONTENT DELIVERY</h2>
  <p class="intro" style="left:510px;top:2079px;width:440px">Early morning delivery of a consolidated, ready-to-consume media coverage</p>
  <ul class="points" style="left:510px;top:2152px;width:445px">
    <li><svg width="13" height="13" viewBox="0 0 13 13"><circle cx="6.5" cy="6.5" r="5.5" fill="none" stroke="#0088cc" stroke-width="1.6"/><path d="M4 6.7l1.8 1.7L9 5" fill="none" stroke="#0088cc" stroke-width="1.6"/></svg>Customised email templates, delivering content in templates designed to meet your needs</li>
    <li><svg width="13" height="13" viewBox="0 0 13 13"><circle cx="6.5" cy="6.5" r="5.5" fill="none" stroke="#0088cc" stroke-width="1.6"/><path d="M4 6.7l1.8 1.7L9 5" fill="none" stroke="#0088cc" stroke-width="1.6"/></svg>Customised platform - modern portal tailored to meet your media management needs, removing the unwanted clutter and focusing on the job at hand</li>
    <li><svg width="13" height="13" viewBox="0 0 13 13"><circle cx="6.5" cy="6.5" r="5.5" fill="none" stroke="#0088cc" stroke-width="1.6"/><path d="M4 6.7l1.8 1.7L9 5" fill="none" stroke="#0088cc" stroke-width="1.6"/></svg>Integration with Intranets, third-party communication tools e.g. team chat, RSS readers, customised APIs</li>
  </ul>

  <!-- Media insights -->
  <h2 class="section-title" style="left:96px;top:2482px">MEDIA INSIGHTS &amp; CONSULTANCY</h2>
  <ul class="points" style="left:96px;top:2553px;width:440px">
    <li><svg width="13" height="13" viewBox="0 0 13 13"><circle cx="6.5" cy="6.5" r="5.5" fill="none" stroke="#0088cc" stroke-width="1.6"/><path d="M4 6.7l1.8 1.7L9 5" fill="none" stroke="#0088cc" stroke-width="1.6"/></svg>Levering the normalised content sets from your integrated monitoring service, we can analyse and tag your coverage based on complex qualitative measurement criteria, consistent across all languages and geographies, to combine with quantitative metrics.</li>
    <li><svg width="13" height="13" viewBox="0 0 13 13"><circle cx="6.5" cy="6.5" r="5.5" fill="none" stroke="#0088cc" stroke-width="1.6"/><path d="M4 6.7l1.8 1.7L9 5" fill="none" stroke="#0088cc" stroke-width="1.6"/></svg>Ability to create a single consistent measurement programme across all of your global operations.</li>
    <li><svg width="13" height="13" viewBox="0 0 13 13"><circle cx="6.5" cy="6.5" r="5.5" fill="none" stroke="#0088cc" stroke-width="1.6"/><path d="M4 6.7l1.8 1.7L9 5" fill="none" stroke="#0088cc" stroke-width="1.6"/></svg>Consultancy to HQ and local offices on how to utilise and align existing measurement and insight initiatives to provide continuity.</li>
    <li><svg width="13" height="13" viewBox="0 0 13 13"><circle cx="6.5" cy="6.5" r="5.5" fill="none" stroke="#0088cc" stroke-width="1.6"/><path d="M4 6.7l1.8 1.7L9 5" fill="none" stroke="#0088cc" stroke-width="1.6"/></svg>Customised online dashboards with near real time data insights, coupled with Board-ready offline reporting and export options.</li>
    <li><svg width="13" height="13" viewBox="0 0 13 13"><circle cx="6.5" cy="6.5" r="5.5" fill="none" stroke="#0088cc" stroke-width="1.6"/><path d="M4 6.7l1.8 1.7L9 5" fill="none" stroke="#0088cc" stroke-width="1.6"/></svg>Integration with social media content, third-party data, point-of-sale, web analytics, and delivering on your Integrated Communications Framework</li>
  </ul>
  <div class="art" role="img" aria-label="Illustration of a person with a laptop sitting on stacked layers surrounded by floating social icons" style="left:578px;top:2560px;width:421px;height:300px;background:linear-gradient(180deg,#eef5fb,#d5e8f5)"></div>
  <svg class="slab" style="left:578px;top:2875px" width="374" height="117" aria-hidden="true"><polygon points="0,0 374,38 374,117 0,79" fill="var(--blue)"/></svg>

  <footer class="footer">
    <h3>VENNATRA</h3>
    <p>Lorem ipsum dolor sit amet, consectetur adipiscing elit, sed do eiusmod tempor incididunt ut labore et dolore magna aliqua</p>
    <ul class="contacts">
      <li><svg width="12" height="16" viewBox="0 0 12 16"><path d="M6 0a6 6 0 0 0-6 6c0 4.5 6 10 6 10s6-5.5 6-10a6 6 0 0 0-6-6zm0 8.4A2.4 2.4 0 1 1 6 3.6a2.4 2.4 0 0 1 0 4.8z" fill="#0a9ae0"/></svg>Lorem ipsum dolor</li>
      <li><svg width="15" height="15" viewBox="0 0 15 15"><path d="M3 0l3 3.5-1.7 2a9 9 0 0 0 4.2 4.2l2-1.7L14 11l-1.5 3C6 14 1 9 0 2.5z" fill="#0a9ae0"/></svg>+1 555 010 2040</li>
      <li><svg width="17" height="12" viewBox="0 0 17 12"><rect width="17" height="12" rx="1" fill="#0a9ae0"/><path d="M0 1l8.5 6L17 1" fill="none" stroke="#262626" stroke-width="1.3"/></svg>info@vennatra.com</li>
    </ul>
    <div class="copy">Copyrights 2019 Vennatra | Al Rights are Reserved</div>
  </footer>
</section>

</body>
</html>
```